Business Card Design for BrightvaleMedia.com

--I need a business card design for my company BrightvaleMedia.com

I have attached my logo...I want the brightvale media logo on the front of the business card, and then I want The Quillstone Chief on the back of it with my information.

I would like to see a light colored background as well as a dark colored background

FRONT:
BRIGHTVALE MEDIA LOGO
248 N. Larkmoor
3rd Floor
San Diego CA 92173
www.BrightvaleMedia.com

Advanced Website & App Development
Websites, Apps, Online Voucher Systems

Leading Edge Marketing Services
SMS, VB, SMM, SEM,

BACK:
QUILLSTONE CHIEF LOGO
Dorian Pelletta
The Quillstone Chief
Call Or Text: 619-555-0148
Dorian@QuillstoneChief.example
www.QuillstoneChief.example

Target Market(s)

small business owners

Industry/Entity Type

Business Consultant

Contact Information for Business Card

FRONT:
BRIGHTVALE MEDIA LOGO
248 N. Larkmoor
3rd Floor
San Diego CA 92173
www.BrightvaleMedia.com

SMS, VB, SMM, SEM,

BACK:
QUILLSTONE CHIEF LOGO
Dorian Pelletta
The Quillstone Chief
Dorian@QuillstoneChief.example
www.QuillstoneChief.example

Requirements
Must have
• add this quote on it somewhere, anywhere,preferrably on back
• "The Fastest Way To Success Is To Take Action”
• — Dorian Pelletta, Quillstone Chief
Nice to have
• open
Should not have
• red

```html
<!DOCTYPE html>
<html lang="en">
<head>
<meta charset="utf-8">
<title>Brightvale Media – Business Card</title>
<link href="https://fonts.googleapis.com/css2?family=Montserrat:wght@400;500;600&family=Oswald:wght@500&display=swap" rel="stylesheet">
<style>
  :root {
    --stage: #2a2a2c;
    --card: #050505;
    --blue: #1f7fc1;
    --white: #f2f2f2;
    --grey: #9a9a9a;
  }
  * { margin: 0; padding: 0; box-sizing: border-box; }
  html, body { width: 1200px; height: 900px; overflow: hidden; }
  body {
    background: var(--stage);
    font-family: "Montserrat", sans-serif;
    color: var(--white);
    position: relative;
  }
  .card {
    position: absolute;
    left: 270px;
    width: 660px;
    height: 377px;
    background: var(--card);
    border-radius: 22px;
    overflow: hidden;
  }
  .card--front { top: 52px; }
  .card--back { top: 471px; }

  /* Front */
  .front-brand {
    position: absolute;
    top: 48px; left: 0; right: 0;
    text-align: center;
  }
  .brand-name {
    font-weight: 600;
    font-size: 40px;
    letter-spacing: 5px;
    color: var(--blue);
    line-height: 1;
    white-space: nowrap;
  }
  .brand-rule {
    display: block;
    width: 440px;
    height: 2px;
    margin: 18px auto 0;
    background: var(--white);
  }
  .front-details {
    position: absolute;
    top: 148px; left: 0; right: 0;
    text-align: center;
    font-size: 17px;
    line-height: 22px;
  }
  .front-details .accent { color: var(--blue); }
  .front-details .gap { height: 18px; }
  .services-heading { color: var(--blue); text-transform: uppercase; }
  .services-list { color: var(--blue); }

  /* Back */
  .back-brand {
    position: absolute;
    top: 104px; left: 48px;
    width: 340px;
  }
  .back-brand .brand-name { font-size: 30px; letter-spacing: 2px; }
  .tagline {
    margin-top: 12px;
    font-family: "Oswald", sans-serif;
    font-weight: 500;
    font-size: 16px;
    line-height: 20px;
    letter-spacing: 0.3px;
    color: var(--blue);
    text-transform: uppercase;
    white-space: nowrap;
  }
  .contact {
    position: absolute;
    top: 200px; right: 40px;
  }
  .contact-name {
    font-weight: 600;
    font-size: 22px;
    line-height: 26px;
    color: var(--blue);
  }
  .contact-role { font-size: 15px; line-height: 20px; margin: 2px 0 8px; }
  .contact-list { list-style: none; font-size: 14px; line-height: 22px; }
  .contact-list li { display: flex; align-items: center; gap: 8px; white-space: nowrap; }
  .contact-list svg { width: 12px; height: 12px; flex: none; fill: var(--blue); }
  .contact-list .accent { color: var(--blue); }
</style>
</head>
<body>

<section class="card card--front">
  <div class="front-brand">
    <div class="brand-name">BRIGHTVALE MEDIA</div>
    <span class="brand-rule"></span>
  </div>
  <div class="front-details">
    <p>248 N. Larkmoor</p>
    <p>3rd Floor</p>
    <p>San Diego CA 92173</p>
    <p>www.<span class="accent">Brightvale</span>Media.com</p>
    <div class="gap"></div>
    <p>Advanced Website &amp; App Development</p>
    <p>Websites, Apps, Online Voucher Systems</p>
    <p class="services-heading">Leading Edge Marketing Services</p>
    <p class="services-list">SMS, VB, SMM, SEM,</p>
  </div>
</section>

<section class="card card--back">
  <div class="back-brand">
    <div class="brand-name">QUILLSTONE CHIEF</div>
    <p class="tagline">The Fastest Way To Success Is To Take Action</p>
  </div>
  <div class="contact">
    <p class="contact-name">Dorian Pelletta</p>
    <p class="contact-role">CEO</p>
    <ul class="contact-list">
      <li>
        <svg viewBox="0 0 24 24" aria-hidden="true"><path d="M6.6 10.8a15.2 15.2 0 0 0 6.6 6.6l2.2-2.2a1 1 0 0 1 1-.25 11.4 11.4 0 0 0 3.6.57 1 1 0 0 1 1 1V20a1 1 0 0 1-1 1A17 17 0 0 1 3 4a1 1 0 0 1 1-1h3.5a1 1 0 0 1 1 1 11.4 11.4 0 0 0 .57 3.6 1 1 0 0 1-.25 1z"/></svg>
        <span>619-555-0148</span>
      </li>
      <li>
        <svg viewBox="0 0 24 24" aria-hidden="true"><path d="M2 5h20v14H2z M4 7v1l8 5 8-5V7l-8 5z" fill-rule="evenodd"/></svg>
        <span>Dorian@QuillstoneChief.example</span>
      </li>
      <li>
        <svg viewBox="0 0 24 24" aria-hidden="true"><path d="M12 2a10 10 0 1 0 0 20 10 10 0 0 0 0-20zm0 2c.9 0 2.2 1.8 2.8 5H9.2C9.8 5.8 11.1 4 12 4zM4.3 11h4.7a22 22 0 0 0 0 2H4.3a8 8 0 0 1 0-2zm6.7 0h2a20 20 0 0 1 0 2h-2a20 20 0 0 1 0-2zm4 0h4.7a8 8 0 0 1 0 2H15a22 22 0 0 0 0-2zm-5.8 4h5.6c-.6 3.2-1.9 5-2.8 5s-2.2-1.8-2.8-5z"/></svg>
        <span>www.<span class="accent">QuillstoneChief</span>.example</span>
      </li>
    </ul>
  </div>
</section>

</body>
</html>
```